Cleaning Service Company In need of Good Web presence.

The company is a cleaning service company which provides professional staff and service for cleaning. This is a project to build a site that is both solid and a strong recognition of our organization. It is supposed to show quality, cleanliness, professionalism. The use of images and art for imagery is all good just to have a site that is consistent and solid. There might be a chance to make stationary, logo and business cars if someone feels they can build a brand that is consistent. The image we are going for is clean solid and to stand out. Finally stationary should not be expensive to print.

Current logo is attached and can be used or can be made more creative.

Target Market(s)

Corporate and Government entities, that will feel that this company has a brand that sets it apart from the rest. The company is new so the modification of the logo will not be an issue if a more solid brand come out of this project. The idea is to have a clean consistent product that stands our from others in terms of website, stationary, etc

Industry/Entity Type

Cleaning Service

Contact Information for Business Card

P.O.Box 51947
Riffa
Kingdom of Bahrain

Logo Text

Harbor Lane Services

Number of Pages Required

4 page

Font styles to use
Sans Serif

Colors
abd036
cadf82
eaf2ce
9bcb3b

Requirements
Must have
• Green Color to be used in order to stick to the name. Also the creativity and boldness in an elegant manner.
Nice to have
• Arabic name of company
• هاربر لين سرفسس ذ.م.م
• if cannot be put at least make a location should be chosen
• Also could be a bit of 3D given to the logo if it could stay elegent.
Should not have
• Should not show people cleaning.

```html
<!DOCTYPE html>
<html lang="en">
<head>
<meta charset="utf-8">
<title>Harbor Lane Services</title>
<link href="https://fonts.googleapis.com/css2?family=Lato:ital,wght@0,400;0,700;0,900;1,400&family=Open+Sans:ital,wght@0,400;0,600;1,400&family=Noto+Naskh+Arabic:wght@500&display=swap" rel="stylesheet">
<style>
:root{
  --green:#8dc63f;
  --green-dark:#7ab332;
  --green-band:#7dbb35;
  --green-soft:#cadf82;
  --ink:#1e1e1e;
  --text:#666;
  --muted:#888;
  --line:#e3e3e3;
  --white:#fff;
}
*{margin:0;padding:0;box-sizing:border-box}
html,body{width:1200px;height:2723px;overflow:hidden;background:var(--white)}
body{position:relative;font-family:"Open Sans",Arial,sans-serif;color:var(--text)}
.abs{position:absolute}

/* header */
.topbar{top:14px;right:95px;display:flex;gap:26px;font:700 13px "Lato",sans-serif;color:var(--ink);align-items:center}
.topbar span{display:flex;align-items:center;gap:10px}
.ico-circle{width:24px;height:24px;border-radius:50%;border:1.5px solid var(--green);display:flex;align-items:center;justify-content:center}
.nav{top:56px;right:95px;display:flex;gap:26px;font:700 14px "Lato",sans-serif;color:var(--ink);align-items:center}
.nav .active{color:var(--green)}
.brand{left:88px;top:8px;width:164px;height:150px;border-radius:50%;background:var(--white);z-index:5;display:flex;align-items:center;justify-content:center;box-shadow:0 2px 6px rgba(0,0,0,.15)}
.brand-name{width:120px;text-align:center;font:900 18px/1.15 "Lato",sans-serif;color:var(--green-dark)}

/* hero */
.hero{top:91px;left:0;width:1200px;height:470px;background:linear-gradient(180deg,#8fa6bd 0%,#a9b8c5 45%,#6f7c86 70%,#c7c1b2 100%)}
.hero-title{top:235px;width:1200px;text-align:center;color:var(--white);text-shadow:0 2px 6px rgba(0,0,0,.35)}
.hero-ar{font:500 52px/1.3 "Noto Naskh Arabic",serif}
.hero-en{font:700 33px/1.3 "Lato",sans-serif;margin-top:4px}
.dots{top:490px;left:0;width:1200px;display:flex;justify-content:center;gap:6px}
.dots i{width:12px;height:12px;border-radius:50%;border:2px solid var(--white)}
.dots i:first-child{background:var(--white)}

/* welcome */
.welcome{top:628px;left:98px;width:480px}
h2.section{font:900 25px "Lato",sans-serif;color:var(--ink);letter-spacing:.3px}
.welcome p{font-size:11.5px;line-height:25px;margin-top:20px}
.btn-outline{display:inline-block;margin-top:26px;border:1px solid #bbb;padding:8px 12px;font:700 11.5px "Lato",sans-serif;color:var(--green)}
.video{top:630px;left:648px;width:452px;height:290px;border:5px solid #f0f0f0;box-shadow:0 0 0 1px #ddd;background:linear-gradient(180deg,#5a95d4 0%,#9ec6ea 45%,#8aa06a 58%,#4f8a2c 100%)}
.play{position:absolute;left:198px;top:117px;width:56px;height:56px;border-radius:50%;background:rgba(0,0,0,.75);display:flex;align-items:center;justify-content:center}

/* services */
.services{top:925px;left:0;width:1200px;height:590px;background:linear-gradient(180deg,#5c6166 0%,#6b6f70 40%,#4d5251 100%)}
.services-shade{top:925px;left:0;width:1200px;height:590px;background:rgba(30,30,30,.35)}
.svc{top:1139px;width:240px;text-align:center;color:var(--white)}
.svc .ring{width:164px;height:164px;margin:0 auto;border-radius:50%;border:2px solid var(--white);display:flex;align-items:center;justify-content:center}
.svc h3{font:700 19px "Lato",sans-serif;margin-top:26px}
.svc p{font-size:11.5px;line-height:19px;margin-top:4px}

/* blog */
.blog-title{top:1512px;width:1200px;text-align:center}
.card{top:1583px;width:324px}
.card .pic{height:214px;border:5px solid #f0f0f0;box-shadow:0 0 0 1px #ddd;position:relative}
.date{position:absolute;left:-5px;bottom:0;width:42px;height:62px;background:var(--green);color:var(--white);text-align:center;font:700 22px/1 "Lato",sans-serif;padding-top:8px}
.date small{display:block;font:400 11px "Lato",sans-serif;margin-top:8px}
.card h3{font:700 19px "Lato",sans-serif;color:var(--ink);margin-top:38px}
.card p{font-size:11.5px;line-height:22px;margin-top:10px;padding-bottom:14px;border-bottom:1px solid var(--line)}
.meta{display:flex;gap:18px;margin-top:14px;font-size:11px;color:var(--text)}
.meta span{display:flex;align-items:center;gap:6px}

/* testimonials */
.testi{top:2026px;left:0;width:1200px;height:334px;background:var(--green-band)}
.quote{top:2156px;width:310px;display:flex;gap:20px;color:var(--white)}
.avatar{flex:none;width:74px;height:74px;border-radius:50%;border:3px solid var(--white);background:linear-gradient(180deg,#d9c7b4,#a48d78)}
.quote p{font:italic 11.5px/24px "Open Sans",sans-serif}
.quote p b{font:700 26px/0 Georgia,serif;vertical-align:-8px;margin-right:6px}
.quote .who{font:700 10.5px "Lato",sans-serif;text-transform:uppercase;margin-top:12px}
.quote .role{font:italic 10px "Open Sans",sans-serif;color:#e8f2d2}
.arrow{top:2175px;width:34px;height:34px;border-radius:50%;border:1.5px solid rgba(255,255,255,.8);display:flex;align-items:center;justify-content:center}

/* footer */
.foot-brand{left:76px;top:2414px;width:226px;height:210px;border-radius:50%;border:6px solid var(--green);display:flex;align-items:center;justify-content:center}
.foot-brand .brand-name{width:170px;font-size:25px}
.fcol{top:2428px}
.fcol h4{font:700 17px "Lato",sans-serif;color:var(--ink);letter-spacing:.3px}
.fcol ul{list-style:none;margin-top:22px;font-size:11.5px;line-height:25px;color:var(--text)}
.fcol p{font-size:11.5px;line-height:20px;margin-top:22px}
.field{margin-top:16px;width:252px;border-bottom:1px solid #ccc;font-size:11px;color:#aaa;padding:8px 0 10px 2px}
.btn{display:inline-block;margin-top:18px;background:var(--green);color:var(--white);font:700 11px "Lato",sans-serif;padding:9px 14px}
.contact li{display:flex;gap:14px;align-items:flex-start;margin-bottom:14px;line-height:18px}
.contact{list-style:none;margin-top:22px;font-size:11.5px}
.contact svg{flex:none;margin-top:2px}
.rule{top:2658px;left:98px;width:1004px;height:1px;background:var(--line)}
.copy{top:2682px;left:98px;font-size:11.5px;color:var(--text)}
.social{top:2674px;left:960px;display:flex;gap:10px}
.social i{width:30px;height:30px;border-radius:50%;border:1.5px solid var(--green)}
</style>
</head>
<body>

<header>
  <div class="abs brand"><div class="brand-name">Harbor Lane Services</div></div>
  <div class="abs topbar">
    <span><i class="ico-circle"><svg width="12" height="12" viewBox="0 0 24 24"><path fill="#8dc63f" d="M6.6 10.8a15 15 0 0 0 6.6 6.6l2.2-2.2c.3-.3.7-.4 1-.2 1.1.4 2.3.6 3.6.6.6 0 1 .4 1 1V20c0 .6-.4 1-1 1A17 17 0 0 1 3 4c0-.6.4-1 1-1h3.5c.6 0 1 .4 1 1 0 1.300.2 2.5.6 3.6.1.3 0 .7-.2 1z"/></svg></i>1 555 014 2200</span>
    <span><i class="ico-circle"><svg width="12" height="12" viewBox="0 0 24 24"><path fill="#8dc63f" d="M2 5h20v14H2z"/><path fill="none" stroke="#fff" stroke-width="2" d="M2 6l10 7 10-7"/></svg></i>info@harborlaneservices.com</span>
  </div>
  <nav class="abs nav">
    <span class="active">HOME</span><span>ABOUT US</span><span>SERVICES</span><span>OFFICE CLEANING</span><span>BLOG</span><span>CONTACT US</span>
    <svg width="14" height="14" viewBox="0 0 24 24"><circle cx="10" cy="10" r="7" fill="none" stroke="#1e1e1e" stroke-width="3"/><path d="M15 15l7 7" stroke="#1e1e1e" stroke-width="3"/></svg>
  </nav>
</header>

<section>
  <div class="abs hero" role="img" aria-label="City skyline with modern towers along the waterfront"></div>
  <svg class="abs" style="top:470px;left:0" width="1200" height="100" viewBox="0 0 1200 100">
    <path d="M0 20 Q600 110 1200 20 L1200 100 L0 100 Z" fill="#8dc63f"/>
    <path d="M0 28 Q600 118 1200 28 L1200 100 L0 100 Z" fill="#fff"/>
  </svg>
  <div class="abs hero-title">
    <div class="hero-ar" lang="ar" dir="rtl">هاربر لين سرفسس ذ.م.م</div>
    <div class="hero-en">Harbor Lane Services LLC</div>
  </div>
  <div class="abs dots"><i></i><i></i><i></i><i></i></div>
</section>

<section>
  <div class="abs welcome">
    <h2 class="section">WELCOME TO HARBOR LANE SERVICES</h2>
    <p>At vero eos et accusamus et iusto odio dignissimos ducimus qui blanditiis praesentium voluptatum deleniti atque corrupti quos dolor.</p>
    <p>Suas molestias excepturi sint occaecati cupiditate non provident, similique sunt in culpa qui officia deserunt mollitia animi, id est laborum et dolorum fuga. Et harum quidemrer um facilis est et expedita distinctio. Nam libero tempore, cum soluta nobis est eligendi optio cumque nihil impedit quo minus id quod maxime.</p>
    <span class="btn-outline">READ MORE &gt;&gt;</span>
  </div>
  <div class="abs video" role="img" aria-label="Video still of a green park lawn in front of city towers">
    <div class="play"><svg width="20" height="22" viewBox="0 0 20 22"><path d="M3 1l16 10L3 21z" fill="#fff"/></svg></div>
  </div>
</section>

<section>
  <div class="abs services" role="img" aria-label="Business district street with palm trees and modern buildings"></div>
  <div class="abs services-shade"></div>
  <svg class="abs" style="top:918px;left:0" width="1200" height="110" viewBox="0 0 1200 110">
    <path d="M0 0 L1200 0 L1200 10 Q600 170 0 10 Z" fill="#fff"/>
    <path d="M0 10 Q600 170 1200 10" fill="none" stroke="#8dc63f" stroke-width="7"/>
  </svg>
  <svg class="abs" style="top:1420px;left:0" width="1200" height="100" viewBox="0 0 1200 100">
    <path d="M0 90 Q600 -60 1200 90 L1200 100 L0 100 Z" fill="#8dc63f"/>
    <path d="M0 98 Q600 -50 1200 98 L1200 100 L0 100 Z" fill="#fff"/>
  </svg>
  <h2 class="abs section" style="top:1078px;width:1200px;text-align:center;color:#fff">OUR SERVICES</h2>

  <div class="abs svc" style="left:85px">
    <div class="ring"><svg width="66" height="66" viewBox="0 0 64 64" fill="none" stroke="#8dc63f" stroke-width="7" stroke-linejoin="round"><path d="M22 20 L32 6 L42 20"/><path d="M50 30 L57 46 L42 54"/><path d="M26 54 L8 52 L14 34"/></svg></div>
    <h3>Organic Cleaning</h3>
    <p>Nam libero tempore, cum soluta nobis<br>est eligendi optio cumque nihi</p>
  </div>
  <div class="abs svc" style="left:348px">
    <div class="ring"><svg width="72" height="62" viewBox="0 0 72 62" fill="#8dc63f"><path d="M36 0 L72 16 L0 16 Z"/><rect x="4" y="19" width="64" height="5"/><rect x="9" y="27" width="8" height="24"/><rect x="23" y="27" width="8" height="24"/><rect x="41" y="27" width="8" height="24"/><rect x="55" y="27" width="8" height="24"/><rect x="2" y="54" width="68" height="8"/></svg></div>
    <h3>Government</h3>
    <p>Nam libero tempore, cum soluta nobis<br>est eligendi optio cumque nihi</p>
  </div>
  <div class="abs svc" style="left:611px">
    <div class="ring"><svg width="70" height="62" viewBox="0 0 24 21"><path fill="#8dc63f" d="M12 21 L2 11 A5.5 5.5 0 0 1 12 3 A5.5 5.5 0 0 1 22 11 Z"/></svg></div>
    <h3>Health/Safety</h3>
    <p>Nam libero tempore, cum soluta nobis<br>est eligendi optio cumque nihi</p>
  </div>
  <div class="abs svc" style="left:873px">
    <div class="ring"><svg width="70" height="58" viewBox="0 0 70 58"><path d="M24 10 V4 H46 V10" fill="none" stroke="#8dc63f" stroke-width="5"/><rect x="0" y="10" width="70" height="48" rx="7" fill="#8dc63f"/><rect x="14" y="10" width="4" height="48" fill="#5b5f60"/><rect x="52" y="10" width="4" height="48" fill="#5b5f60"/></svg></div>
    <h3>Corporate</h3>
    <p>Nam libero tempore, cum soluta nobis<br>est eligendi optio cumque nihi</p>
  </div>
</section>

<section>
  <h2 class="abs section blog-title">LATEST BLOG</h2>

  <article class="abs card" style="left:96px">
    <div class="pic" role="img" aria-label="Business people talking outside a modern tower" style="background:linear-gradient(160deg,#dfe6ef,#b9c4d3 55%,#c9c2b6)"><div class="date">01<small>NOV</small></div></div>
    <h3>Finibus Bonorum et Malorum</h3>
    <p>Nam libero tempore, cum soluta nobis est eligendi optio cumque nihil impedit quo minus id quod maxim.</p>
    <div class="meta"><span><svg width="11" height="11" viewBox="0 0 12 12" fill="#8dc63f"><circle cx="6" cy="3.5" r="3"/><path d="M0 12a6 5 0 0 1 12 0z"/></svg>Sam Rowe</span><span><svg width="13" height="11" viewBox="0 0 14 12" fill="none" stroke="#8dc63f" stroke-width="1.5"><path d="M1 1h10v7H5l-3 3V8H1z"/></svg>3 Comments</span></div>
  </article>
  <article class="abs card" style="left:439px">
    <div class="pic" role="img" aria-label="Tablet, coffee cup and notebook on a wooden desk" style="background:linear-gradient(135deg,#7b4f2c,#a8784c 45%,#3b3b3b 70%,#8d6340)"><div class="date">01<small>NOV</small></div></div>
    <h3>Finibus Bonorum et Malorum</h3>
    <p>Nam libero tempore, cum soluta nobis est eligendi optio cumque nihil impedit quo minus id quod maxim.</p>
    <div class="meta"><span><svg width="11" height="11" viewBox="0 0 12 12" fill="#8dc63f"><circle cx="6" cy="3.5" r="3"/><path d="M0 12a6 5 0 0 1 12 0z"/></svg>Sam Rowe</span><span><svg width="13" height="11" viewBox="0 0 14 12" fill="none" stroke="#8dc63f" stroke-width="1.5"><path d="M1 1h10v7H5l-3 3V8H1z"/></svg>3 Comments</span></div>
  </article>
  <article class="abs card" style="left:782px">
    <div class="pic" role="img" aria-label="Glass facade of a tall office building" style="background:linear-gradient(160deg,#9fc3e6,#4f7fb3 50%,#6e9cc8)"><div class="date">01<small>NOV</small></div></div>
    <h3>Finibus Bonorum et Malorum</h3>
    <p>Nam libero tempore, cum soluta nobis est eligendi optio cumque nihil impedit quo minus id quod maxim.</p>
    <div class="meta"><span><svg width="11" height="11" viewBox="0 0 12 12" fill="#8dc63f"><circle cx="6" cy="3.5" r="3"/><path d="M0 12a6 5 0 0 1 12 0z"/></svg>Sam Rowe</span><span><svg width="13" height="11" viewBox="0 0 14 12" fill="none" stroke="#8dc63f" stroke-width="1.5"><path d="M1 1h10v7H5l-3 3V8H1z"/></svg>3 Comments</span></div>
  </article>
</section>

<section>
  <div class="abs testi"></div>
  <h2 class="abs section" style="top:2083px;width:1200px;text-align:center;color:#fff">CLIENT TESTIMONIALS</h2>
  <div class="abs arrow" style="left:30px"><svg width="10" height="12" viewBox="0 0 10 12"><path d="M8 1L2 6l6 5" fill="none" stroke="#fff" stroke-width="1.5"/></svg></div>
  <div class="abs arrow" style="left:1134px"><svg width="10" height="12" viewBox="0 0 10 12"><path d="M2 1l6 5-6 5" fill="none" stroke="#fff" stroke-width="1.5"/></svg></div>

  <div class="abs quote" style="left:96px">
    <div class="avatar" role="img" aria-label="Client portrait"></div>
    <div><p><b>&ldquo;</b>At vero eos et accusamus et iustodio dignissimos ducimus qui blanditiipraesnt ium voluptatum deleniti atque crupquos dolores et quas molestias.</p>
    <div class="who">Marisa Holt</div><div class="role">Financial Services Professional</div></div>
  </div>
  <div class="abs quote" style="left:440px">
    <div class="avatar" role="img" aria-label="Client portrait"></div>
    <div><p><b>&ldquo;</b>At vero eos et accusamus et iustodio dignissimos ducimus qui blanditiipraesnt ium voluptatum deleniti atque crupquos dolores et quas molestias.</p>
    <div class="who">Daniel R. Okafor</div><div class="role">National Urban Fellow at the Harbor</div></div>
  </div>
  <div class="abs quote" style="left:784px">
    <div class="avatar" role="img" aria-label="Client portrait"></div>
    <div><p><b>&ldquo;</b>At vero eos et accusamus et iustodio dignissimos ducimus qui blanditiipraesnt ium voluptatum deleniti atque crupquos dolores et quas molestias.</p>
    <div class="who">Lena Varga</div><div class="role">Creative Strategist | Entrepreneur &amp; Upcoming</div></div>
  </div>
</section>

<footer>
  <div class="abs foot-brand"><div class="brand-name">Harbor Lane Services</div></div>

  <div class="abs fcol" style="left:379px">
    <h4>INFORMATION</h4>
    <ul><li>Home</li><li>About us</li><li>Services</li><li>Office Cleaning</li><li>Blog</li><li>Contact Us</li></ul>
  </div>
  <div class="abs fcol" style="left:577px">
    <h4>NEWSLETTER SUBSCRIPTION</h4>
    <p>Regsiter your Email Address to get<br>informaion about us</p>
    <div class="field">Email Address</div>
    <span class="btn">SUBSCRIBE</span>
  </div>
  <div class="abs fcol" style="left:906px">
    <h4>CONTACT US</h4>
    <ul class="contact">
      <li><svg width="12" height="14" viewBox="0 0 12 16"><path fill="#8dc63f" d="M6 0a6 6 0 0 1 6 6c0 4-6 10-6 10S0 10 0 6a6 6 0 0 1 6-6z"/><circle cx="6" cy="6" r="2.2" fill="#fff"/></svg><span>48 Alder Street<br>Rochester NY 14620, US</span></li>
      <li><svg width="13" height="13" viewBox="0 0 24 24"><path fill="#8dc63f" d="M6.6 10.8a15 15 0 0 0 6.6 6.6l2.2-2.2c.3-.3.7-.4 1-.2 1.1.4 2.3.6 3.6.6.6 0 1 .4 1 1V20c0 .6-.4 1-1 1A17 17 0 0 1 3 4c0-.6.4-1 1-1h3.5c.6 0 1 .4 1 1 0 1.3.2 2.5.6 3.6.1.3 0 .7-.2 1z"/></svg><span>1 555 014 2200</span></li>
      <li><svg width="14" height="13" viewBox="0 0 14 13"><rect x="0" y="4" width="14" height="9" rx="1" fill="#8dc63f"/><rect x="3" y="0" width="8" height="5" fill="none" stroke="#8dc63f" stroke-width="1.5"/><rect x="3" y="7" width="8" height="2" fill="#fff"/></svg><span>1 555 014 2211</span></li>
      <li><svg width="14" height="11" viewBox="0 0 24 18"><path fill="#8dc63f" d="M0 0h24v18H0z"/><path fill="none" stroke="#fff" stroke-width="2" d="M0 1l12 8 12-8"/></svg><span>info@harborlaneservices.com</span></li>
    </ul>
  </div>

  <div class="abs rule"></div>
  <div class="abs copy">Copyrights © 2017, Harbor Lane Services, Inc. All rights reserved. Terms &amp; Condition.</div>
  <div class="abs social"><i></i><i></i><i></i><i></i></div>
</footer>

</body>
</html>
```